Business Card for a Dental Office

The design should communicate integrity, quality and reliability. We also want the card look elegant, simple, but still stand out, different from the traditional-dental-office business card.

Industry/Entity Type

Business

```html
<!DOCTYPE html>
<html lang="en">
<head>
<meta charset="utf-8">
<title>Harlow Dental Studio – Business Card</title>
<link rel="stylesheet" href="https://fonts.googleapis.com/css2?family=Oswald:wght@500;600;700&family=Open+Sans:wght@400;600&display=swap">
<style>
  :root {
    --backdrop: #e9e4da;
    --card-white: #fbfbfa;
    --gold: #a88838;
    --tagline-gold: #c2a032;
    --ink: #111111;
    --paper-text: #ffffff;
  }
  * { margin: 0; padding: 0; box-sizing: border-box; }
  html, body {
    width: 1200px;
    height: 1022px;
    overflow: hidden;
    background: var(--backdrop);
  }
  .card {
    position: absolute;
    left: 150px;
    top: 254px;
    width: 900px;
    height: 514px;
    background: var(--card-white);
    border-radius: 22px;
    overflow: hidden;
    box-shadow: 0 18px 40px rgba(60, 45, 20, 0.25);
  }
  .card-bands {
    position: absolute;
    inset: 0;
    width: 900px;
    height: 514px;
  }
  .brand {
    position: absolute;
    left: 70px;
    top: 112px;
    display: flex;
    align-items: center;
    gap: 22px;
  }
  .brand-square {
    width: 86px;
    height: 86px;
    background: var(--gold);
  }
  .brand-name {
    font-family: "Oswald", sans-serif;
    font-weight: 700;
    font-size: 54px;
    line-height: 1;
    letter-spacing: 0.5px;
    color: var(--ink);
    text-transform: uppercase;
  }
  .brand-tagline {
    margin-top: 8px;
    font-family: "Oswald", sans-serif;
    font-weight: 500;
    font-size: 21px;
    letter-spacing: 3.2px;
    color: var(--tagline-gold);
    text-transform: uppercase;
  }
  .person {
    position: absolute;
    right: 40px;
    top: 228px;
    text-align: right;
  }
  .person-name {
    font-family: "Oswald", sans-serif;
    font-weight: 600;
    font-size: 40px;
    line-height: 1.05;
    color: var(--paper-text);
    letter-spacing: 1px;
    text-transform: uppercase;
  }
  .person-role {
    font-family: "Oswald", sans-serif;
    font-weight: 500;
    font-size: 19px;
    letter-spacing: 2px;
    color: var(--tagline-gold);
    text-transform: uppercase;
  }
  .contact {
    position: absolute;
    left: 44px;
    bottom: 22px;
    list-style: none;
    font-family: "Open Sans", sans-serif;
    font-size: 19px;
    color: var(--paper-text);
  }
  .contact li {
    display: flex;
    align-items: center;
    gap: 12px;
    line-height: 28px;
  }
  .contact svg {
    width: 17px;
    height: 17px;
    flex: none;
  }
</style>
</head>
<body>
  <article class="card">
    <svg class="card-bands" viewBox="0 0 900 514" aria-hidden="true">
      <defs>
        <linearGradient id="goldBand" x1="0" y1="0" x2="1" y2="1">
          <stop offset="0" stop-color="#9c7c30"/>
          <stop offset="0.55" stop-color="#a88838"/>
          <stop offset="1" stop-color="#8a6a24"/>
        </linearGradient>
      </defs>
      <path class="band-gold" d="M0 380 H484 L540 338 H900 V514 H0 Z" fill="url(#goldBand)"/>
      <path class="band-black" d="M590 214 H900 V314 H540 Z" fill="#111111"/>
      <polyline class="band-rule" points="0,368 470,368 528,324" fill="none" stroke="#111111" stroke-width="4"/>
    </svg>

    <div class="brand">
      <div class="brand-square"></div>
      <div class="brand-text">
        <div class="brand-name">Harlow Dental Studio</div>
        <div class="brand-tagline">Your smile is your gift to others</div>
      </div>
    </div>

    <div class="person">
      <div class="person-name">Daniel Reyes</div>
      <div class="person-role">Director</div>
    </div>

    <ul class="contact">
      <li>
        <svg viewBox="0 0 24 24" fill="#ffffff"><path d="M6.6 10.8a15.2 15.2 0 0 0 6.6 6.6l2.2-2.2a1 1 0 0 1 1-.25 11.4 11.4 0 0 0 3.6.57 1 1 0 0 1 1 1V20a1 1 0 0 1-1 1A17 17 0 0 1 3 4a1 1 0 0 1 1-1h3.5a1 1 0 0 1 1 1c0 1.25.2 2.46.57 3.6a1 1 0 0 1-.25 1z"/></svg>
        +330 5120-4470
      </li>
      <li>
        <svg viewBox="0 0 24 24" fill="none" stroke="#ffffff" stroke-width="2"><rect x="3" y="5" width="18" height="14"/><path d="M3 6l9 7 9-7"/></svg>
        info@harlowdentalstudio.com
      </li>
      <li>
        <svg viewBox="0 0 24 24" fill="none" stroke="#ffffff" stroke-width="2"><circle cx="12" cy="12" r="9"/><path d="M3 12h18M12 3c3 3 3 15 0 18M12 3c-3 3-3 15 0 18"/></svg>
        www.harlowdentalstudio.com
      </li>
    </ul>
  </article>
</body>
</html>
```